Bramwell IT Services Business Card

Bramwell IT Services are a Perth based IT Services company. We would like to incorporate our company logo (attached) and stick with the blue that is in that design. I would like a clean look design that isn't too busy, yet creates a lasting image that is instantly recognisable in the recipients mind.

Target Market(s)

The target audience is small/medium business owners.

Industry/Entity Type

Business

Font styles to use
Serif
Sans Serif

Colors

Designer to choose colors to be used in the design.

Requirements
Must have
• The design should include:
Business name: Bramwell IT Services
Directors Name: Marcus Tenley
Phone Number: 0483 562 904
Email: support@bramwellit.com.au
Website: www.bramwellit.com.au

```html
<!DOCTYPE html>
<html lang="en">
<head>
<meta charset="utf-8">
<title>Bramwell IT Services Business Card</title>
<link href="https://fonts.googleapis.com/css2?family=Exo+2:wght@400;600;700&display=swap" rel="stylesheet">
<style>
  :root{
    --backdrop:#e4e6e9;
    --card:#ffffff;
    --card-shade:#f1f2f4;
    --brand-blue:#1f7fe0;
    --band-light:#5cc3f5;
    --band-deep:#1b82e2;
    --ink:#3c3f44;
    --corner-dark:#3a3b3d;
    --chip:#ffffff;
  }
  *{margin:0;padding:0;box-sizing:border-box}
  html,body{width:1200px;height:974px;overflow:hidden}
  body{background:var(--backdrop);font-family:"Exo 2",sans-serif;position:relative}
  .card{position:absolute;left:240px;width:720px;height:411px;background:linear-gradient(160deg,var(--card) 40%,var(--card-shade));overflow:hidden;box-shadow:0 6px 18px rgba(0,0,0,.15)}
  .card--front{top:51px}
  .card--back{top:512px}
  .corner-bar{position:absolute;background:var(--corner-dark)}
  .corner-bar--top{top:0;right:0;width:150px;height:14px}
  .corner-bar--right{top:0;right:0;width:14px;height:70px}
  .corner-bar--bottom{bottom:0;left:0;width:150px;height:14px}
  .corner-bar--left{bottom:0;left:0;width:14px;height:70px}
  .brand{position:absolute;display:flex;align-items:center;gap:14px;color:var(--brand-blue);font-weight:700;text-transform:uppercase;white-space:nowrap}
  .brand-mark{width:22px;height:22px;background:var(--brand-blue)}
  .card--front .brand{left:50%;top:50%;transform:translate(-50%,-50%);font-size:34px}
  .card--back .brand{left:200px;top:72px;font-size:26px}
  .card--back .brand .brand-mark{width:18px;height:18px}
  .band{position:absolute;inset:0}
  .person{position:absolute;left:40px;top:152px}
  .person-name{font-size:26px;font-weight:600;color:var(--ink);text-transform:uppercase;letter-spacing:.5px}
  .person-role{font-size:17px;color:var(--brand-blue);margin-top:2px}
  .contact-list{position:absolute;list-style:none;color:#fff;font-size:16px}
  .contact-list li{display:flex;align-items:center;gap:12px;height:40px}
  .contact-list--details{left:40px;top:245px}
  .contact-list--web{left:470px;top:180px}
  .chip{width:24px;height:24px;background:var(--chip);border-radius:3px;display:flex;align-items:center;justify-content:center;flex:none}
  .chip svg{width:16px;height:16px}
</style>
</head>
<body>
  <section class="card card--front">
    <span class="corner-bar corner-bar--top"></span>
    <span class="corner-bar corner-bar--right"></span>
    <div class="brand"><span class="brand-mark"></span>Bramwell IT Services</div>
    <span class="corner-bar corner-bar--bottom"></span>
    <span class="corner-bar corner-bar--left"></span>
  </section>

  <section class="card card--back">
    <svg class="band" width="720" height="411" viewBox="0 0 720 411">
      <defs>
        <linearGradient id="bandFill" x1="0" y1="0" x2="1" y2="0">
          <stop offset="0" stop-color="var(--band-light)"/>
          <stop offset="1" stop-color="var(--band-deep)"/>
        </linearGradient>
      </defs>
      <polygon points="0,232 720,120 720,411 0,411" fill="url(#bandFill)"/>
    </svg>
    <div class="brand"><span class="brand-mark"></span>Bramwell IT Services</div>
    <div class="person">
      <div class="person-name">Marcus Tenley</div>
      <div class="person-role">Managing Director</div>
    </div>
    <ul class="contact-list contact-list--details">
      <li><span class="chip"><svg viewBox="0 0 16 16"><path d="M8 1a5 5 0 0 0-5 5c0 4 5 9 5 9s5-5 5-9a5 5 0 0 0-5-5zm0 7a2 2 0 1 1 0-4 2 2 0 0 1 0 4z" fill="var(--band-deep)"/></svg></span>14 Hay Street Perth</li>
      <li><span class="chip"><svg viewBox="0 0 16 16"><path d="M4 1l2.5 3-1.5 2c1 2 2.5 3.5 4.5 4.5l2-1.5 3 2.5-1.5 2.5C8 13.5 2.5 8 1.5 2.5z" fill="var(--band-deep)"/></svg></span>0483 562 904</li>
      <li><span class="chip"><svg viewBox="0 0 16 16"><rect x="1.5" y="3.5" width="13" height="9" fill="none" stroke="var(--band-deep)" stroke-width="1.6"/><path d="M1.5 3.5L8 9l6.5-5.5" fill="none" stroke="var(--band-deep)" stroke-width="1.6"/></svg></span>support@bramwellit.com.au</li>
    </ul>
    <ul class="contact-list contact-list--web">
      <li><span class="chip"></span>www.bramwellit.com.au</li>
      <li><span class="chip"></span>www.chirpnest.com</li>
      <li><span class="chip"></span>www.friendwall.com</li>
    </ul>
  </section>
</body>
</html>
```